Corporate Business Card

Very professional, Modern, Not to busy, include phone address email, website
(253) 617-4930, 18761 52nd Avenue S, Kent, WA 98047, martin@plumlinegroup.com, varkoworks.com

Target Market(s)

Manufacturing

Industry/Entity Type

Aero, machining, manufacturing, Off road racing

Contact Information for Business Card

Phone, address email, website

```html
<!DOCTYPE html>
<html lang="en">
<head>
<meta charset="utf-8">
<title>Varko Works – Business Card</title>
<link href="https://fonts.googleapis.com/css2?family=Source+Sans+3:wght@400;600;700&display=swap" rel="stylesheet">
<style>
  :root {
    --navy: #16356b;
    --red: #d2232a;
    --text-gray: #5b5b5b;
    --card-white: #ffffff;
    --backdrop: #e9e9e9;
  }
  * { box-sizing: border-box; margin: 0; padding: 0; }
  html, body {
    width: 1200px; height: 1200px; overflow: hidden;
    background: var(--backdrop);
    font-family: "Source Sans 3", "Myriad Pro", sans-serif;
  }
  .canvas { position: relative; width: 1200px; height: 1200px; }
  .card {
    position: absolute; left: 232px; width: 736px; height: 452px;
    border-radius: 44px; overflow: hidden;
  }
  .card-front { top: 116px; background: var(--card-white); }
  .card-back { top: 632px; background: var(--navy); }

  .front-waves { position: absolute; inset: 0; width: 100%; height: 100%; }

  .brand-name {
    position: absolute; font-weight: 700; letter-spacing: 1px; white-space: nowrap;
  }
  .card-front .brand-name {
    left: 48px; top: 206px; width: 296px; text-align: center;
    font-size: 44px; line-height: 52px; color: var(--navy);
  }
  .card-back .brand-name {
    left: 0; right: 0; top: 180px; text-align: center;
    font-size: 84px; line-height: 96px; color: var(--card-white);
  }

  .divider {
    position: absolute; left: 376px; top: 114px; width: 2px; height: 226px;
    background: var(--navy);
  }
  .contact { position: absolute; left: 402px; top: 108px; }
  .person-name {
    font-size: 36px; line-height: 40px; font-weight: 400; color: var(--red);
    letter-spacing: -0.3px;
  }
  .person-title {
    font-size: 23px; line-height: 28px; color: var(--navy); margin-top: 2px;
  }
  .address {
    font-size: 20px; line-height: 26px; color: var(--text-gray); margin-top: 16px;
  }
  .contact-list { list-style: none; margin-top: 8px; }
  .contact-list li {
    display: flex; align-items: center; height: 30px;
    font-size: 20px; color: var(--text-gray);
  }
  .contact-list svg { width: 20px; height: 20px; margin-right: 14px; flex: none; }
</style>
</head>
<body>
<main class="canvas">
  <section class="card card-front" aria-label="Business card front">
    <svg class="front-waves" viewBox="0 0 736 452" preserveAspectRatio="none" aria-hidden="true">
      <path d="M0 360 Q 360 480 736 400 L736 452 L0 452 Z" fill="var(--red)"/>
      <path d="M160 403 Q 470 452 736 376 L736 393 Q 470 464 160 405 Z" fill="var(--navy)"/>
    </svg>

    <div class="brand-name">VARKO WORKS</div>

    <div class="divider"></div>

    <div class="contact">
      <h1 class="person-name">DARIUS COLE</h1>
      <p class="person-title">President</p>
      <p class="address">18761 52nd Avenue S,<br>Kent, WA 98047</p>
      <ul class="contact-list">
        <li>
          <svg viewBox="0 0 24 24" aria-hidden="true"><path fill="var(--navy)" d="M6.6 10.8a15.1 15.1 0 0 0 6.6 6.6l2.2-2.2c.3-.3.7-.4 1-.2 1.1.4 2.3.6 3.6.6.6 0 1 .4 1 1V20c0 .6-.4 1-1 1A17 17 0 0 1 3 4c0-.6.4-1 1-1h3.5c.6 0 1 .4 1 1 0 1.3.2 2.5.6 3.6.1.3 0 .7-.2 1z"/></svg>
          (253) 617-4930
        </li>
        <li>
          <svg viewBox="0 0 24 24" aria-hidden="true"><rect x="2" y="5" width="18" height="13" fill="var(--navy)"/><path d="M2 5l9 7 9-7" fill="none" stroke="#fff" stroke-width="1.6"/><circle cx="19" cy="18" r="4.5" fill="var(--navy)" stroke="#fff" stroke-width="1.2"/><path d="M17 18l1.5 1.5 2.5-2.8" fill="none" stroke="#fff" stroke-width="1.3"/></svg>
          martin@plumlinegroup.com
        </li>
        <li>
          <svg viewBox="0 0 24 24" aria-hidden="true"><g fill="none" stroke="var(--navy)" stroke-width="1.6"><circle cx="12" cy="12" r="9.5"/><ellipse cx="12" cy="12" rx="4" ry="9.5"/><path d="M2.5 12h19M4 7h16M4 17h16"/></g></svg>
          varkoworks.com
        </li>
      </ul>
    </div>
  </section>

  <section class="card card-back" aria-label="Business card back">
    <div class="brand-name">VARKO WORKS</div>
  </section>
</main>
</body>
</html>
```